The Polish & Glow Studio Website Update

Hello. I am seeking to freshen up my website with a clean and easy feel that incorporates our modern chic style. Our services cater to mostly young professionals and modern moms.

We focus on natural nail care and gentle professional waxing. We are known for our cleanliness. Our clients like our current website, however I'm hoping to make it look even more professional and user friendly. Some clients have even said our current website feels welcoming, unlike other websites that in they feel give a snobbish vibe. I like clean lines, simple, fresh, and sometimes bold. Totally NOT a fan of whimsical.

I threw added an accent color to the color pallet...however it should be used in moderation. I am also open to other accent colors. I'd like the site to emphasize the Brazilian wax as much as nails, if not more than nail. The photos downloaded are just to give you a few images of who we are, however are not necessary. Current website www.thepolishandglowstudio.example

Target Market(s)

Females 30-55

Industry/Entity Type

Beauty Salon

Coding

Coded - Design and coding required

Number of Pages Required

5+ page

Font styles to use
Sans Serif

Colors
ffffff
1b1b1b
acd136
eeeeee
878787
c4c4c4
efefef
7f7f7f

Requirements
Must have
• Clean look
Nice to have
• Our logo
Should not have
• Whimsical

```html
<!DOCTYPE html>
<html lang="en">
<head>
<meta charset="utf-8">
<title>The Polish &amp; Glow Studio</title>
<link href="https://fonts.googleapis.com/css2?family=Raleway:wght@400;500;600&family=Open+Sans:wght@400;600&family=Noto+Serif:wght@700&display=swap" rel="stylesheet">
<style>
:root{
  --white:#ffffff;
  --ink:#1b1b1b;
  --lime:#acd136;
  --lime-dark:#8fb224;
  --mist:#eeeeee;
  --grey:#878787;
  --silver:#c4c4c4;
  --paper:#efefef;
  --slate:#7f7f7f;
}
*{margin:0;padding:0;box-sizing:border-box}
html,body{width:1200px;height:3103px;overflow:hidden}
body{position:relative;background:var(--white);font-family:"Open Sans",Arial,sans-serif;color:var(--ink)}
.abs{position:absolute}
/* header */
.brand{left:99px;top:36px;font-family:"Raleway",sans-serif;font-weight:500;font-size:30px;color:var(--ink);display:flex;align-items:center;gap:12px}
.brand .dot{width:22px;height:22px;border-radius:50%;background:var(--lime)}
.info{top:36px;display:flex;align-items:center;gap:14px;font-size:13px;line-height:21px;color:#555}
.info .ic{width:36px;height:36px;border-radius:50%;display:flex;align-items:center;justify-content:center}
.nav{left:99px;top:103px;width:1001px;height:58px;background:var(--lime);display:flex;justify-content:space-around;align-items:center;padding:0 20px;z-index:3;border-bottom:4px solid var(--lime-dark)}
.nav a{color:var(--white);text-decoration:none;font-size:13.5px;position:relative}
.nav a.current::after{content:"";position:absolute;left:50%;bottom:-22px;margin-left:-7px;border:7px solid transparent;border-bottom-color:var(--white)}
/* hero */
.hero{left:0;top:132px;width:1200px;height:540px;background:var(--ink);overflow:hidden}
.hero-photo{right:0;top:40px;width:540px;height:440px;background:radial-gradient(ellipse at 40% 55%,#e7c3a8 0%,#b88c6f 30%,rgba(90,70,150,.6) 55%,rgba(27,27,27,0) 75%),radial-gradient(circle at 80% 20%,#f3c51e 0,rgba(243,197,30,0) 35%)}
.hero h1{left:97px;top:250px;font-family:"Raleway",sans-serif;font-weight:400;font-size:66px;color:var(--white)}
.hero p{left:99px;top:352px;width:400px;font-family:"Raleway",sans-serif;font-size:19px;line-height:36px;color:var(--white)}
.btn-hero{left:99px;top:461px;width:141px;height:42px;border-radius:21px;background:var(--lime);border:2px solid var(--white);color:var(--white);font-family:"Raleway",sans-serif;font-size:17px;display:flex;align-items:center;justify-content:center}
.dots{left:555px;top:466px;display:flex;gap:14px}
.dots span{width:13px;height:13px;border-radius:50%;border:2px solid var(--white)}
.dots span.on{background:var(--lime);border-color:var(--lime)}
.wave{left:0;bottom:-1px;width:1200px;height:70px}
/* headings */
.sec-title{display:flex;align-items:center;gap:14px;font-family:"Raleway",sans-serif;font-size:38px;font-weight:400}
.sec-title .mark{width:46px;height:46px;border-radius:50%;border:6px solid var(--lime);background:var(--white)}
.sec-title b{font-weight:400;color:var(--lime)}
.rule{height:2px;width:150px;background:var(--ink)}
/* services */
.service{width:278px;height:278px;border-radius:50%;border:2px solid var(--slate);background:var(--white);text-align:center;padding-top:76px}
.service.featured{background:var(--lime);border-color:var(--lime);color:var(--white)}
.service .badge{position:absolute;left:50%;top:-36px;margin-left:-36px;width:72px;height:72px;border-radius:50%;background:var(--lime);border:4px solid var(--white);display:flex;align-items:center;justify-content:center}
.service.featured .badge{background:var(--ink)}
.service h3{font-family:"Raleway",sans-serif;font-weight:500;font-size:19px;margin-bottom:20px}
.service p{font-size:13px;line-height:22px;width:200px;margin:0 auto;color:#555}
.service.featured p{color:var(--white)}
.service .more{display:inline-block;margin-top:14px;padding:7px 16px;border:1.5px solid var(--grey);border-radius:18px;font-size:12.5px;color:#555}
.service.featured .more{border-color:var(--white);color:var(--white)}
/* prices */
.prices{left:0;top:1119px;width:1200px;height:437px;background:linear-gradient(90deg,#0d0d0d,#1b1b1b 45%,#1b1b1b 55%,#0d0d0d)}
.model{left:434px;top:0;width:290px;height:437px;background:radial-gradient(ellipse at 50% 45%,#8a4a2a 0%,#5a2c17 40%,rgba(27,27,27,0) 72%)}
.prices h4{font-family:"Noto Serif",serif;font-size:22px;color:var(--lime)}
.price{font-family:"Noto Serif",serif;font-size:19px;color:var(--white);border-bottom:1px solid var(--slate);padding-bottom:10px;display:flex;gap:14px;align-items:baseline}
.price em{font-style:normal;color:var(--lime);font-size:22px}
.price.right{justify-content:flex-end}
/* about */
.about-text{left:99px;top:1672px;width:610px;font-size:13.5px;line-height:22px;color:#333}
.about-text h5{font-family:"Raleway",sans-serif;font-weight:500;font-size:18px;color:var(--ink);margin-bottom:14px}
.about-text p{margin-bottom:12px}
.about-photo{left:770px;top:1603px;width:330px;height:410px;background:linear-gradient(180deg,#d7dbe0 0%,#9ea5ab 45%,#3b3d40 100%)}
/* gallery */
.gallery{left:0;top:2052px;width:1200px;height:424px;background:radial-gradient(ellipse at 15% 30%,#3c2a45 0%,#1d1a28 50%,#14121a 100%)}
.shot{width:311px;height:248px;border:5px solid var(--white)}
/* contact */
.field{left:99px;width:466px;height:46px;border:1.5px solid var(--silver);font-size:12px;color:var(--grey);padding:13px 12px}
.send{left:631px;top:2718px;width:143px;height:44px;background:var(--lime);color:var(--white);font-size:13.5px;display:flex;align-items:center;justify-content:center}
.reach{top:2834px;display:flex;align-items:center;gap:22px;font-size:13.5px;line-height:25px;color:#333}
.reach .ic{width:78px;height:78px;border-radius:50%;background:var(--lime);border:5px solid var(--mist);display:flex;align-items:center;justify-content:center}
/* footer */
.footer{left:0;top:2930px;width:1200px;height:173px}
.footer-brand{left:99px;top:2990px;font-family:"Raleway",sans-serif;font-size:38px;color:var(--white);display:flex;align-items:center;gap:14px}
.footer-brand .dot{width:40px;height:40px;border-radius:50%;border:5px solid var(--white)}
.copy{left:99px;top:3060px;font-size:13px;color:var(--white)}
.social{left:932px;top:3056px;display:flex;gap:14px}
.social span{width:32px;height:32px;border-radius:50%;border:2px solid var(--white)}
</style>
</head>
<body>

<header>
  <div class="abs brand"><span>The Polish &amp; Glow Studio</span></div>
  <div class="abs info" style="left:604px">
    <span class="ic" style="background:var(--lime)"><svg width="16" height="20" viewBox="0 0 16 20"><path d="M8 0a7 7 0 0 0-7 7c0 5 7 13 7 13s7-8 7-13a7 7 0 0 0-7-7z" fill="#fff"/><circle cx="8" cy="7" r="2.6" fill="#acd136"/></svg></span>
    <span>42 Linden Avenue<br>Millbrook, CT 06000</span>
  </div>
  <div class="abs info" style="left:836px">
    <span class="ic" style="background:var(--ink)"><svg width="16" height="20" viewBox="0 0 16 20"><path d="M8 0a7 7 0 0 0-7 7c0 5 7 13 7 13s7-8 7-13a7 7 0 0 0-7-7z" fill="#fff"/><circle cx="8" cy="7" r="2.6" fill="#1b1b1b"/></svg></span>
    <span>Tuesday - Sunday 9.00 am - 7.00 pm<br>Saturday &amp; Monday Closed</span>
  </div>
  <nav class="abs nav">
    <a class="current">Home</a><a>Schedule An Appointment</a><a>Products and Services</a><a>Careers</a><a>Specials</a><a>About Us</a><a>FAQ</a><a>Contact Us</a>
  </nav>
</header>

<section class="abs hero">
  <div class="abs hero-photo" role="img" aria-label="Bare feet with manicured toes resting among purple iris and yellow calla lily flowers"></div>
  <h1 class="abs">Polish &amp; Glow</h1>
  <p class="abs">Facials are now available at The Polish &amp; Glow Studio</p>
  <div class="abs btn-hero">Book Now</div>
  <div class="abs dots"><span></span><span class="on"></span><span></span><span></span></div>
  <svg class="abs wave" viewBox="0 0 1200 70" preserveAspectRatio="none"><path d="M0 0 C300 70 600 70 900 35 C1020 20 1120 20 1200 40 L1200 70 L0 70 Z" fill="#fff"/></svg>
</section>

<section>
  <div class="abs sec-title" style="left:458px;top:676px"><span class="mark"></span><span><b>O</b>ur <b>S</b>ervices</span></div>
  <div class="abs rule" style="left:580px;top:733px"></div>

  <div class="abs service" style="left:132px;top:781px">
    <div class="badge"><svg width="30" height="30" viewBox="0 0 30 30"><rect x="9" y="10" width="12" height="16" rx="2" fill="#fff"/><rect x="12" y="4" width="6" height="6" fill="#fff"/></svg></div>
    <h3>Gel Polish Manicures</h3>
    <p>Maintain your beautiful Gel Manicure and save with this series of 6 Gel Polish Manicures</p>
    <span class="more">Read More</span>
  </div>
  <div class="abs service featured" style="left:461px;top:781px">
    <div class="badge"><svg width="30" height="30" viewBox="0 0 30 30"><path d="M8 28V12a7 7 0 0 1 14 0v16z" fill="#fff"/></svg></div>
    <h3>Brazilian Waxes</h3>
    <p>Maintain your beautiful Gel Manicure and save with this series of 6 Gel Polish Manicures</p>
    <span class="more">Read More</span>
  </div>
  <div class="abs service" style="left:790px;top:781px">
    <div class="badge"><svg width="30" height="30" viewBox="0 0 30 30"><path d="M15 3c-4 6-6 9-6 12a6 6 0 0 0 12 0c0-3-2-6-6-12z" fill="#fff"/><path d="M3 24h24" stroke="#fff" stroke-width="3"/></svg></div>
    <h3>Chemical Peel</h3>
    <p>Maintain your beautiful Gel Manicure and save with this series of 6 Gel Polish Manicures</p>
    <span class="more">Read More</span>
  </div>
</section>

<section class="abs prices">
  <div class="abs model" role="img" aria-label="Woman with long glossy auburn hair"></div>
  <h4 class="abs" style="left:292px;top:30px">Wax</h4>
  <h4 class="abs" style="left:874px;top:30px">Nails</h4>
  <div class="abs price" style="left:178px;top:96px;width:400px"><em>$13</em>Brow Design</div>
  <div class="abs price" style="left:186px;top:173px;width:370px"><em>$10</em>Chin</div>
  <div class="abs price" style="left:206px;top:249px;width:340px"><em>$10</em>Lip</div>
  <div class="abs price" style="left:178px;top:336px;width:300px"><em>$55</em>Brazilian</div>
  <div class="abs price right" style="left:680px;top:121px;width:365px">Gel Polish Manicure<em>$34</em></div>
  <div class="abs price right" style="left:700px;top:216px;width:330px">Hair Dressing<em>$24</em></div>
  <div class="abs price right" style="left:720px;top:301px;width:325px">Signature Pedicure<em>$40</em></div>
</section>

<section>
  <div class="abs sec-title" style="left:99px;top:1593px;font-size:32px"><span class="mark" style="width:38px;height:38px;border-width:5px"></span><span><b>A</b>bout <b>P</b>olish &amp; <b>G</b>low</span></div>
  <div class="abs rule" style="left:155px;top:1642px;width:110px"></div>
  <div class="abs about-text">
    <h5>Who We Are</h5>
    <p>The Polish &amp; Glow Studio is a small nail spa located in Millbrook, CT, between Eastfield and Northport. Our spa includes 1 private treatment room, 2 nail stations, and 2 pedicure stations.</p>
    <p>Our specialties include the Brazilian Bikini Wax, Chemical Peel, and Gel Polish Manicure. All of our staff are licensed or certified as Nail Technicians and/or Estheticians. They are all friendly and knowledgeable, ready to answer any questions you may have regarding your skin.</p>
    <h5 style="margin-top:6px">What they say...</h5>
    <p>"Maria is a doll! She did a wonderful job on my eyebrows. She took her time, was very thorough, and made them look beautiful. I will definitely ask for her again!"</p>
    <p>"The intimacy of the salon made me feel completely pampered; I didn't have to share with anyone except my daughter!"</p>
  </div>
  <div class="abs about-photo" role="img" aria-label="Bright salon interior with nail stations and polish shelves"></div>
</section>

<section class="abs gallery" role="img" aria-label="Close-up of hands with purple nail polish">
  <div class="abs sec-title" style="left:488px;top:22px;font-size:32px;color:var(--white)"><span class="mark" style="width:38px;height:38px;border-width:5px"></span><span><b>O</b>ur <b>G</b>allery</span></div>
  <div class="abs rule" style="left:540px;top:72px;width:120px;background:var(--white)"></div>
  <div class="abs shot" style="left:99px;top:131px;background:linear-gradient(135deg,#f4ebe6,#e0c2b4)" role="img" aria-label="Manicured hands"></div>
  <div class="abs shot" style="left:445px;top:131px;background:linear-gradient(135deg,#7fd3ec,#2ca8cf 60%,#d9b39a)" role="img" aria-label="Woman relaxing in a turquoise swimsuit"></div>
  <div class="abs shot" style="left:790px;top:131px;background:linear-gradient(180deg,#d9dbdc,#8e958b 60%,#5b6d3a)" role="img" aria-label="Private treatment room with a green covered bed"></div>
</section>

<section>
  <div class="abs sec-title" style="left:99px;top:2506px;font-size:32px"><span><b>C</b>ontact <b>U</b>s</span></div>
  <div class="abs rule" style="left:99px;top:2552px;width:70px"></div>
  <div class="abs field" style="top:2582px">Your Name</div>
  <div class="abs field" style="top:2650px">Email Address</div>
  <div class="abs field" style="top:2718px">Subject</div>
  <div class="abs field" style="left:631px;top:2582px;width:469px;height:114px">Message</div>
  <div class="abs send">Send Message</div>

  <div class="abs reach" style="left:102px">
    <span class="ic"><svg width="26" height="26" viewBox="0 0 24 24"><path d="M6.6 10.8a15 15 0 0 0 6.6 6.6l2.2-2.2a1 1 0 0 1 1-.25 11 11 0 0 0 3.6.6 1 1 0 0 1 1 1V20a1 1 0 0 1-1 1A17 17 0 0 1 3 4a1 1 0 0 1 1-1h3.5a1 1 0 0 1 1 1 11 11 0 0 0 .6 3.6 1 1 0 0 1-.25 1z" fill="#fff"/></svg></span>
    <span>(555) 014-2250<br>(555) 014-7731 (Free Call)</span>
  </div>
  <div class="abs reach" style="left:464px">
    <span class="ic"><svg width="28" height="22" viewBox="0 0 28 22"><rect x="1" y="1" width="26" height="20" rx="2" fill="#fff"/><path d="M2 3l12 9 12-9" stroke="#acd136" stroke-width="2.5" fill="none"/></svg></span>
    <span>info@thepolishandglowstudio.example<br>www.polishandglow.example</span>
  </div>
  <div class="abs reach" style="left:822px">
    <span class="ic"><svg width="22" height="28" viewBox="0 0 16 20"><path d="M8 0a7 7 0 0 0-7 7c0 5 7 13 7 13s7-8 7-13a7 7 0 0 0-7-7z" fill="#fff"/><circle cx="8" cy="7" r="2.6" fill="#acd136"/></svg></span>
    <span>42 Linden Avenue<br>Millbrook, CT 06000</span>
  </div>
</section>

<footer>
  <svg class="abs footer" viewBox="0 0 1200 173" preserveAspectRatio="none"><path d="M0 30 C250 0 450 10 650 28 C850 46 1050 40 1200 18 L1200 173 L0 173 Z" fill="#acd136"/><path d="M0 30 C250 0 450 10 650 28 C850 46 1050 40 1200 18 L1200 30 C1050 50 850 56 650 38 C450 20 250 12 0 40 Z" fill="#8fb224"/></svg>
  <div class="abs footer-brand"><span class="dot"></span><span>Polish &amp; Glow</span></div>
  <div class="abs copy">© 2016 Polish &amp; Glow. All Rights Reserved</div>
  <div class="abs social"><span></span><span></span><span></span><span></span></div>
</footer>

</body>
</html>
```